"The Orginal LoopPeg's" needs a Package Design!! Everybody's got a LoopPeg, What's Yours?

I need eye popping packaging design!! My LoopPeg's are gonna be big! I'm a single mom I'm based in AZ, so this is big for me. The LoopPeg's keep towels off the floor & so much more!! Color cardboard insert background, bright yellow and Bright blue, like a caribbean blue, funky font for the Product Name. The Original, can be smaller and in an easy script. I have some pictures so you can get an concept and basic design ideas. There are no limits to their uses!! Please call me for any questions or direction.
Updates

I want to thank you all for participating, You each brought a different perspective and had some really good ideas. I will definitely us this service again! Thank you, Dolores Fitzwick

Target Market(s)

Mom's, woman, men, students you name it!!

Colors
fbee3e
0293ce

Requirements
Must have
• Clear pvc packaging so you can see the product and they have to hang over so you see how they are used. The look needs to draw people in to it!! Read my instructions on the downloaded pics and info and if you have questions please let me know. The towel and towel bar can be like a drawing not actual towel picture. On the reverse side is a list of ideas and my website. Other colors for lettering aside from the Caribbean blue for the word "LoopPeg's" is up to you, use your expertise.
Should not have
• The blue is not on the color wheel that is shown here.

```html
<!DOCTYPE html>
<html lang="en">
<head>
<meta charset="utf-8">
<title>The Orginal LoopPeg's – Package Insert</title>
<link href="https://fonts.googleapis.com/css2?family=Arimo:wght@700&family=Bangers&family=Fredoka:wght@500;600&family=Lilita+One&display=swap" rel="stylesheet">
<style>
  :root {
    --yellow: #fbee3e;
    --yellow-glow: #fffbd0;
    --blue: #0293ce;
    --blue-deep: #1f8fd0;
    --red: #e8262b;
    --red-text: #e31e24;
    --white: #ffffff;
    --stage: #eeeae4;
    --product-a: #c7336b;
    --product-b: #2e8fc4;
  }
  * { box-sizing: border-box; margin: 0; padding: 0; }
  html, body { width: 1200px; height: 1200px; overflow: hidden; }
  body { background: var(--stage); position: relative; font-family: "Fredoka", sans-serif; }

  .card {
    position: absolute; top: 258px; height: 658px; background: var(--yellow);
    box-shadow: 0 4px 14px rgba(0,0,0,.18);
  }
  .card--front { left: 34px; width: 549px;
    background: radial-gradient(ellipse 60% 45% at 50% 55%, var(--yellow-glow), var(--yellow) 70%); }
  .card--back { left: 623px; width: 547px; }

  /* Front */
  .brand { position: absolute; top: 40px; left: 0; width: 100%; text-align: center;
    color: var(--blue); font-weight: 600; line-height: 1; }
  .brand__small { font-size: 26px; display: block; margin-bottom: 6px; }
  .brand__name { font-size: 70px; letter-spacing: 1px; display: inline-flex; align-items: center; gap: 14px; }
  .brand__dot { width: 18px; height: 18px; border-radius: 50%; background: var(--blue); }

  .tagline-band { position: absolute; top: 162px; left: 0; width: 100%; height: 66px;
    background: var(--blue-deep); color: var(--white); font-family: "Arimo", sans-serif;
    font-size: 19px; text-align: center; line-height: 27px; padding-top: 6px; }

  .product-art { position: absolute; top: 240px; left: 116px; width: 318px; height: 150px; border-radius: 10px;
    background: linear-gradient(115deg, var(--product-a), var(--product-b) 50%, var(--product-a)); opacity: .85; }

  .icon-box { position: absolute; top: 378px; width: 82px; height: 82px; border: 4px solid var(--blue);
    border-radius: 6px; background: var(--yellow-glow); }
  .icon-box--pvc { left: 158px; }
  .icon-box--hang { left: 288px; }
  .pvc-sheet { position: absolute; left: 18px; top: 10px; width: 38px; height: 54px; border: 2px solid #555;
    font: 11px "Arimo", sans-serif; color: #333; display: flex; align-items: center; justify-content: center; }
  .hang-art { position: absolute; inset: 10px; background: linear-gradient(var(--blue), var(--product-a)); opacity: .6; border-radius: 3px; }
  .step-arrow { position: absolute; left: 242px; top: 408px; }

  .slogan { position: absolute; top: 470px; left: 40px; width: 468px; height: 106px; background: var(--red);
    border: 4px solid var(--white); box-shadow: 0 3px 8px rgba(0,0,0,.2);
    font-family: "Bangers", sans-serif; color: var(--white); font-size: 38px; line-height: 40px;
    text-align: center; padding-top: 12px; letter-spacing: 1px; }
  .count-badge { position: absolute; top: 518px; left: 438px; width: 92px; height: 92px; border-radius: 50%;
    background: var(--blue); border: 3px solid var(--white); color: var(--white);
    font: 700 12px/15px "Arimo", sans-serif; text-align: center; padding-top: 30px; }
  .count-badge small { font-size: 10px; display: block; }
  .note { position: absolute; top: 592px; left: 0; width: 100%; text-align: center;
    font: 700 13px "Arimo", sans-serif; color: var(--red-text); }

  /* Back */
  .uses-head { position: absolute; top: 64px; left: 30px; width: 487px; text-align: center;
    font-family: "Lilita One", sans-serif; color: var(--blue); font-size: 15px; line-height: 22px; letter-spacing: .6px; }
  .uses-head .hot { color: var(--red-text); font-size: 22px; }
  .uses-photos { position: absolute; top: 136px; left: 36px; display: flex; gap: 13px; }
  .uses-photo { width: 113px; height: 124px; border: 5px solid var(--blue); border-radius: 8px; }
  .uses-photo--bib { background: linear-gradient(#b9785e, #6aa6d8); }
  .uses-photo--bar { background: linear-gradient(#f4f4f4, #c0283a 70%, #f4f4f4); }
  .uses-photo--wrap { background: linear-gradient(#e7d6c5, #a9d27a); }
  .uses-photo--shade { background: linear-gradient(#8a6a4f 35%, #c9dce8 35%); }

  .uses-list { position: absolute; top: 286px; list-style: none; color: var(--blue); font-size: 15.5px;
    font-weight: 500; line-height: 21.2px; }
  .uses-list--left { left: 59px; }
  .uses-list--right { left: 283px; }
  .uses-list li { display: flex; align-items: center; gap: 7px; }
  .tick { width: 13px; height: 13px; border: 1.5px solid var(--blue); background: var(--white); flex: none; }

  .closing { position: absolute; top: 546px; left: 0; width: 100%; text-align: center;
    font-family: "Lilita One", sans-serif; color: var(--red-text); font-size: 21px; letter-spacing: .8px; }
  .site { position: absolute; top: 581px; left: 0; width: 100%; text-align: center;
    font: 700 12px "Arimo", sans-serif; color: var(--red-text); }
</style>
</head>
<body>
  <section class="card card--front">
    <div class="brand"><span class="brand__small">The Orginal</span><span class="brand__name"><span class="brand__dot"></span>LoopPeg's</span></div>
    <div class="tagline-band">NO MORE TOWELS ON THE FLOOR<br>&amp; SO MUCH MORE!!!</div>
    <div class="product-art" role="img" aria-label="Two polka-dot straps with round-ended clips hanging over a bar"></div>
    <div class="icon-box icon-box--pvc"><div class="pvc-sheet">PVC</div></div>
    <svg class="step-arrow" width="40" height="20" viewBox="0 0 40 20"><path d="M2 10h26" stroke="#f39a1e" stroke-width="4"/><path d="M26 2l12 8-12 8z" fill="#f39a1e"/></svg>
    <div class="icon-box icon-box--hang"><div class="hang-art" role="img" aria-label="Strap hung over a bar icon"></div></div>
    <div class="slogan">EVERYBODY'S GOT A LOOPPEG<br>WHAT'S YOURS?</div>
    <div class="count-badge">4 LOOPPEGS<small>per box</small></div>
    <p class="note">Thin clear rubber band to hold product in place.</p>
  </section>

  <section class="card card--back">
    <p class="uses-head"><span class="hot">ENDLESS USES</span> – POST A PICTURE OF YOUR LOOPPEG IDEA TO OUR WEBSITE AND YOU COULD WIN A <span class="hot">FREE</span> PACKAGE OF LIMITED EDITION LOOPPEGS'!!</p>
    <div class="uses-photos">
      <div class="uses-photo uses-photo--bib" role="img" aria-label="Toddler wearing a towel bib"></div>
      <div class="uses-photo uses-photo--bar" role="img" aria-label="Red towel clipped to a bar"></div>
      <div class="uses-photo uses-photo--wrap" role="img" aria-label="Green towel wrap"></div>
      <div class="uses-photo uses-photo--shade" role="img" aria-label="Clip used as a shade pull"></div>
    </div>
    <ul class="uses-list uses-list--left">
      <li><span class="tick"></span>Baby Bibs</li>
      <li><span class="tick"></span>Baby Strollers</li>
      <li><span class="tick"></span>Hanging Bathing Suits</li>
      <li><span class="tick"></span>By the Pool</li>
      <li><span class="tick"></span>Pull downs for Shades</li>
      <li><span class="tick"></span>Tarp Holders</li>
      <li><span class="tick"></span>Camping</li>
      <li><span class="tick"></span>Room Dividers</li>
      <li><span class="tick"></span>College Dorms</li>
      <li><span class="tick"></span>The Gym</li>
      <li><span class="tick"></span>Photography Backdrops</li>
      <li><span class="tick"></span>Traveling</li>
    </ul>
    <ul class="uses-list uses-list--right">
      <li><span class="tick"></span>Towel wraps</li>
      <li><span class="tick"></span>Pet Training</li>
      <li><span class="tick"></span>Drying Lingerie</li>
      <li><span class="tick"></span>Tablecloths</li>
      <li><span class="tick"></span>Dishtowels</li>
      <li><span class="tick"></span>The Garage</li>
      <li><span class="tick"></span>Hanging Quilts</li>
      <li><span class="tick"></span>To hold your pants closed</li>
      <li><span class="tick"></span>Curtains (no sewing!)</li>
      <li><span class="tick"></span>Valences (no sewing!)</li>
      <li><span class="tick"></span>Drapes (no sewing!)</li>
      <li><span class="tick"></span>Shower Curtains</li>
    </ul>
    <p class="closing">THE ONLY LIMIT IS YOUR IMAGINATION</p>
    <p class="site">The original LoopPegs'.com</p>
  </section>
</body>
</html>
```